July 2022 Industrial Manufacturer Product Expo Mexico City

We manufacture large screws and fastners for large Mining equipment, Trains, large ships, airplanes, wind turbines, and so on. We also do custom work base on the customer needs. No matter the size we can make it.
We have a Expo coming up with companies all over the world. We have to stand out we are a family own business so our customer service will be above and beyond anyone can provide. We do not have a sales force to push our products and services we provide one on one service.
Plus@!! I'm looking for anything that you designers can come up with if it was your company to put on a business card, plus i want to do a 1 or 2 sided pamphlet, and then a website. We make Speciality Bolts for large mining equipment these bolts can be 3 to 4 foot long!!! Plus fasteners, Nuts, washers, any, size, strengths, special materials, we offer more of a ono on one customer service, We are a small company, family own, but can fulfill any type of orders. We can also provide special time lines for emergency orders. "We keep the machines running we here at KRV don't believe in down time" We want to hear any slogan based on our company to stand out.
Thanks i really appreciate all your work and options that we have to pick on. Plus just a thought we could possibly want to entertain a experience Marketing internet help maybe a employment possibility. Thanks

I need 2 cards one in Spanish and English Like the steel back ground maybe send me in some bright red and blue writing Same with the Black cards Please remove the word Military The logo KRV maybe integrate a picture of a Bolt 🔩 Thank you

Still looking for I need 2 cards one in Spanish and English Like the steel back ground maybe send me in some bright red and blue writing Same with the Black cards try bright writing Please remove the word Military The logo KRV maybe integrate a picture of a Bolt 🔩 Plus will need the company to make a brochure and website next Thank you

Target Market(s)

Large Mining, Ship, Train, Green Energy, VELM, and Government equipment. Throughout the World

Industry/Entity Type

We can Custom Manufacture any type of Fastners for Mining equipment, Trains, Ships, Green energy, Governments, or military projects. wind turbines,

Contact Information for Business Card

I attached the name and contact info that's on a card, plus the Company Logo. Would like industrial looking background with Bright Colors that will stand out!! If we can insert somewhere maybe on back that we "Custom Manufacture Any Size or Quantity Fastners for Large Mining Equipment, Trains, Ships, Green Energy Equipment or Government Projects

Font styles to use
Other font styles liked:
• You Pick, has to be bold, colorful standout, Professional looking Beable to read it.

Colors

Designer to choose colors to be used in the design.

Requirements
Must have
• Need in Spanish and English TO STANDOUT FROM THE REST OF THE EXPO!! See Business card details, Rounded corners
Nice to have
• Can i see some of the darker cards with Bright Red and Blue letters I like to see the different type of card material, heavy thickness, plastic, transparent, Metal types, Bright Colors, I saw like Raised letters like on the logo.

```html
<!DOCTYPE html>
<html lang="es">
<head>
<meta charset="utf-8">
<title>KRV – Tarjetas de presentación</title>
<link href="https://fonts.googleapis.com/css2?family=Tinos:wght@400;700&display=swap" rel="stylesheet">
<style>
  :root {
    --stage: #e4e4e4;
    --steel-light: #f7f7f7;
    --steel-mid: #e6e8ea;
    --card-blue: #0b6aaf;
    --card-blue-deep: #095a96;
    --ink-dark: #1d2a6b;
    --ink-light: #1b8fd6;
    --ink-grey: #3a3a3a;
    --accent-red: #e3202a;
    --white: #ffffff;
  }
  * { box-sizing: border-box; margin: 0; padding: 0; }
  html, body { width: 1200px; height: 930px; overflow: hidden; }
  body {
    background: var(--stage);
    font-family: "Tinos", "Times New Roman", serif;
    position: relative;
  }
  .card {
    position: absolute;
    width: 540px;
    height: 309px;
    border-radius: 14px;
    box-shadow: 0 10px 24px rgba(0,0,0,0.12);
    display: flex;
    flex-direction: column;
    align-items: center;
    text-align: center;
  }
  .card--front {
    left: 50px;
    top: 450px;
    background: linear-gradient(135deg, var(--steel-light) 0%, var(--steel-mid) 55%, var(--steel-light) 100%);
    padding-top: 40px;
  }
  .card--back {
    left: 610px;
    top: 170px;
    background: linear-gradient(135deg, var(--card-blue) 0%, var(--card-blue-deep) 100%);
    color: var(--white);
    padding-top: 62px;
  }
  .brand {
    font-weight: 700;
    letter-spacing: 0.12em;
    line-height: 1;
  }
  .card--front .brand {
    font-size: 64px;
    color: var(--ink-grey);
    margin-bottom: 18px;
  }
  .card--back .brand {
    font-size: 92px;
    color: var(--white);
    margin-bottom: 26px;
  }
  .holder {
    color: var(--ink-light);
    font-size: 21px;
    margin-bottom: 10px;
  }
  .role {
    color: var(--ink-dark);
    font-size: 16px;
  }
  .divider {
    width: 70px;
    height: 1px;
    background: var(--accent-red);
    margin: 7px auto;
  }
  .email {
    color: var(--ink-dark);
    font-size: 16px;
  }
  .phones {
    color: var(--ink-dark);
    font-size: 16px;
    display: flex;
    gap: 10px;
    align-items: center;
  }
  .phones .label { color: var(--accent-red); font-weight: 700; }
  .phones .sep { width: 1px; height: 16px; background: var(--accent-red); }
  .tagline {
    font-size: 15px;
    line-height: 1.3;
    max-width: 430px;
  }
</style>
</head>
<body>
  <section class="card card--back" lang="en" aria-label="Card back">
    <div class="brand">KRV</div>
    <p class="tagline">Custom Manufacture Any Size or Quantity Fastners for Large Mining Equipment, Trains, Ships, Green Energy Equipment or Government Projects</p>
  </section>

  <section class="card card--front" aria-label="Frente de tarjeta">
    <div class="brand">KRV</div>
    <p class="holder">Lic. Marisol Ortega Vidal</p>
    <p class="role">Cotizaciones en</p>
    <div class="divider"></div>
    <p class="email">krv.ventas@correo.mx</p>
    <div class="divider"></div>
    <p class="phones">
      <span><span class="label">P:</span> 5550193601</span>
      <span class="sep"></span>
      <span><span class="label">M:</span> 5550827600</span>
    </p>
  </section>
</body>
</html>
```